New Zealand Marlborough Sauvignon Blanc wine packaging design

We need packaging design for our new wine brand, Dunmore Vale. The wine is a New Zealand Marlborough Sauvignon Blanc. We would like the packaging will portray elegance and style with an understated label. We are looking for a label that portrays the elegance of the French Riviera. The label should be round or pill shaped.
Updates

Industry/Entity Type

Wine

Font styles to use
Serif
Sans Serif

Requirements
Must have
• The words in order of importance: Dunmore Vale, Sauvignon Blanc, Marlborough, New Zealand. It should be fit to the bottle posted in the links
Nice to have
• a pill shape or circular shape
Should not have
• Illustrations of wine bottles, wine glasses, or grapes

```html
<!DOCTYPE html>
<html lang="en">
<head>
<meta charset="utf-8">
<title>Dunmore Vale – Sauvignon Blanc Label</title>
<link rel="stylesheet" href="https://fonts.googleapis.com/css2?family=Federo&family=Montserrat:wght@500;600&family=Open+Sans:wght@300&display=swap">
<style>
  :root {
    --bg-top: #f4f4f4;
    --bg-bottom: #d9d9d9;
    --label-black: #0b0b0b;
    --pattern-dark: #1c1c1c;
    --pattern-mid: #2b2b2b;
    --gold: #c59a4e;
    --gold-light: #e3c27e;
    --ivory: #f6f1e6;
  }
  * { margin: 0; padding: 0; box-sizing: border-box; }
  html, body { width: 1200px; height: 1180px; overflow: hidden; }
  body {
    background: linear-gradient(180deg, var(--bg-top), var(--bg-bottom));
    display: flex; align-items: center; justify-content: center;
  }
  .wine-label { width: 760px; height: 960px; display: block; }
  .label-since { font-family: "Montserrat", sans-serif; font-weight: 500; font-size: 20px; letter-spacing: 6px; fill: var(--gold); }
  .label-variety { font-family: "Montserrat", sans-serif; font-weight: 600; font-size: 16px; letter-spacing: 5px; fill: var(--ivory); }
  .label-brand { font-family: "Federo", serif; font-size: 84px; fill: var(--ivory); stroke: var(--gold); stroke-width: 1.5; paint-order: stroke; }
  .label-region { font-family: "Montserrat", sans-serif; font-weight: 600; font-size: 20px; letter-spacing: 6px; fill: var(--ivory); }
  .label-volume { font-family: "Open Sans", sans-serif; font-weight: 300; font-size: 40px; fill: var(--gold); }
</style>
</head>
<body>
  <svg class="wine-label" viewBox="0 0 760 960" role="group" aria-label="Dunmore Vale Sauvignon Blanc wine label">
    <defs>
      <path id="label-shape" d="M0 330 C0 80 180 0 380 0 C580 0 760 80 760 330 L760 830 Q760 960 630 960 L130 960 Q0 960 0 830 Z"/>
      <clipPath id="label-clip"><use href="#label-shape"/></clipPath>
      <radialGradient id="pattern-tone" cx="50%" cy="45%" r="65%">
        <stop offset="0" stop-color="var(--pattern-mid)"/>
        <stop offset="0.6" stop-color="var(--pattern-dark)"/>
        <stop offset="1" stop-color="var(--label-black)"/>
      </radialGradient>
    </defs>

    <use href="#label-shape" fill="var(--label-black)"/>
    <g clip-path="url(#label-clip)">
      <rect class="label-pattern" x="0" y="0" width="760" height="960" fill="url(#pattern-tone)" role="img" aria-label="Dark black-on-black damask scroll pattern"/>
    </g>
    <use href="#label-shape" fill="none" stroke="var(--gold)" stroke-width="3" transform="translate(16 16) scale(0.958 0.967)"/>

    <g class="since-badge">
      <line x1="170" y1="150" x2="255" y2="150" stroke="var(--gold)" stroke-width="1.5"/>
      <line x1="505" y1="150" x2="590" y2="150" stroke="var(--gold)" stroke-width="1.5"/>
      <rect x="262" y="130" width="236" height="40" rx="20" fill="none" stroke="var(--gold)" stroke-width="2"/>
      <text class="label-since" x="383" y="157" text-anchor="middle">SINCE 1970</text>
    </g>

    <g clip-path="url(#label-clip)">
      <g class="name-band" transform="rotate(-10 380 500)">
        <line x1="-40" y1="395" x2="800" y2="395" stroke="var(--gold)" stroke-width="2"/>
        <text class="label-variety" x="110" y="432">SAUVIGNON BLANC</text>
        <text class="label-brand" x="380" y="518" text-anchor="middle" textLength="580" lengthAdjust="spacingAndGlyphs">DUNMORE VALE</text>
        <line x1="-40" y1="545" x2="800" y2="545" stroke="var(--gold)" stroke-width="2"/>
        <text class="label-region" x="380" y="588" text-anchor="middle">• MARLBOROUGH, NEW ZEALAND •</text>
        <line x1="-40" y1="615" x2="800" y2="615" stroke="var(--gold)" stroke-width="2"/>
      </g>
    </g>

    <text class="label-volume" x="380" y="860" text-anchor="middle">750ml</text>
  </svg>
</body>
</html>
```